Specialised investor in e-mobility and energy wants business card design

We need a business card design that fits our existing corporate design. <The look and feel must be 'sharp'/'clean', dynamic, communicate momentum, professionalism etc (as one would imagine from a firm in the financial sector). We like the idea of a reverse-side of the card that includes the logo, and the name and contact details on the other. We expect the deliverable to be whatever format might be required to be able to get cards printed directly by a service such as kelmo press. Our website is www.zub.capital

```html
<!DOCTYPE html>
<html lang="en">
<head>
<meta charset="utf-8">
<title>ZUB Capital – Business Card</title>
<link href="https://fonts.googleapis.com/css2?family=Montserrat:wght@400;500;700&display=swap" rel="stylesheet">
<style>
  :root {
    --backdrop: #e9e4dc;
    --card-white: #ffffff;
    --brand-dark: #2e4d22;
    --brand-accent: #7ab648;
    --text-dark: #1f1f1f;
    --logo-reverse: #b4c3a2;
  }
  * { margin: 0; padding: 0; box-sizing: border-box; }
  html, body {
    width: 900px; height: 1200px; overflow: hidden;
    background: var(--backdrop);
    font-family: "Montserrat", Arial, sans-serif;
  }
  .canvas { position: relative; width: 900px; height: 1200px; }
  .card {
    position: absolute; left: 80px; width: 742px; height: 440px;
    border-radius: 32px;
  }
  .card-front { top: 132px; background: var(--card-white); }
  .card-back { top: 638px; background: var(--brand-dark); }

  .wordmark {
    position: absolute; white-space: nowrap;
    font-weight: 500; letter-spacing: 0.5px;
  }
  .card-front .wordmark {
    left: 22px; top: 66px; font-size: 60px; color: var(--brand-dark);
  }
  .card-back .wordmark {
    left: 0; right: 0; top: 160px; text-align: center;
    font-size: 80px; color: var(--logo-reverse);
  }

  .holder { position: absolute; left: 37px; top: 268px; }
  .holder-name { font-size: 26px; font-weight: 700; color: var(--brand-dark); line-height: 1.15; }
  .holder-role { font-size: 15px; font-weight: 400; color: var(--text-dark); }

  .divider {
    position: absolute; left: 40px; top: 331px; width: 666px; height: 2px;
    background: var(--brand-accent);
  }

  .contact-list { position: absolute; left: 36px; top: 353px; list-style: none; }
  .contact-list li {
    display: flex; align-items: center; gap: 10px;
    font-size: 16px; color: var(--text-dark); height: 22px;
  }
  .contact-list svg { width: 14px; height: 14px; fill: var(--brand-accent); }

  .address {
    position: absolute; left: 470px; top: 377px;
    font-size: 16px; color: var(--text-dark); line-height: 21px;
  }
</style>
</head>
<body>
<main class="canvas">
  <section class="card card-front">
    <div class="wordmark">ZUB Capital</div>

    <div class="holder">
      <div class="holder-name">Martin Delacroix</div>
      <div class="holder-role">Owner</div>
    </div>

    <div class="divider"></div>

    <ul class="contact-list">
      <li>
        <svg viewBox="0 0 16 16" aria-hidden="true"><path d="M2 5c0-1.5 2.5-2.5 6-2.5S14 3.5 14 5v1.2h-3V5H5v1.2H2z M4 7h8l1.5 6h-11z"/></svg>
        +41 79514 2087
      </li>
      <li>
        <svg viewBox="0 0 16 16" aria-hidden="true"><path d="M1 3.5h14v1L8 9 1 4.5z M1 6l7 4.5L15 6v6.5H1z"/></svg>
        martin@zub.capital
      </li>
      <li>
        <svg viewBox="0 0 16 16" aria-hidden="true"><circle cx="8" cy="8" r="7"/></svg>
        www.zub.capital.com
      </li>
    </ul>

    <div class="address">
      240 Harbor Lane, Suite 310<br>
      Ardmore, PA 19003
    </div>
  </section>

  <section class="card card-back">
    <div class="wordmark">ZUB Capital</div>
  </section>
</main>
</body>
</html>
```